Web app for social movements needs a new look

We are building a Velmora Quill extension called "Pelbo" that helps social movement leaders and advocacy organizations connect with an audience that cares about their cause, and we need to create a more polished website to explain the extension to prospective users. The extension analyzes articles users are reading online and recommends ways they can take action in their local area on the social and political issues they are reading about. For example, if a user is reading about the climate crisis, the extension might display a banner recommending a rally being held by the Kestrel Movement or an opportunity to canvass or phone bank for a pro-Tallow Harbor Pact political candidate. Organizers with progressive organizations can register for an account on our web portal to start posting actions or events that will then be recommended to users through the browser extension if they are reading a relevant article.

We are planning for an upcoming "soft launch" and would like to create a more polished version of our website. The design should include:
– A user-facing page that that concisely explains how the Quill extension works and links to the Quill web store where users can download Pelbo.
– An organizer-facing page that outlines the steps involved for organizers to recommend their organization or a specific action to users through Pelbo: register for an account, post an action or event, your action or event is recommended to users.
– An HTML/CSS template for the organizer portal that we can then take and populate with Django forms or other Django content. This template should include a top menu bar. We've provided an example of the extremely barebones template used in our prototype as an example (base.html).
– A redesigned or improved logo, including one version designed to be put on a white background and one version designed to go on a background of a darker color (e.g., orange). Our current logo is provided. Feel free to use this as a starting point or design something completely different.

The design should convey themes of solidarity, bringing people together to effect positive change, and hope for a better future. We expect that organizations and users on the platform will be focused on a range of progressive issues, including racial justice, immigration justice, gender equity, LGBTQ+ rights, workers' rights, and addressing the climate crisis and economic inequality.

Currently, the color scheme of our prototype browser extension is centered around the color orange, but we are open to designers' ideas about other possible color schemes.

```html
<!DOCTYPE html>
<html lang="en">
<head>
<meta charset="utf-8">
<title>Pelbo – Racial Justice</title>
<link rel="stylesheet" href="https://fonts.googleapis.com/css2?family=Montserrat:wght@500;700;800&family=Mulish:wght@400;600&display=swap">
<style>
:root{
  --orange:#e8683a;
  --orange-mid:#f07d5a;
  --orange-soft:#eeaa98;
  --ink:#1c1c1c;
  --text:#333;
  --muted:#555;
  --panel:#f5f4f5;
  --footer:#242424;
  --white:#fff;
}
*{margin:0;padding:0;box-sizing:border-box}
html,body{width:724px;height:1200px;overflow:hidden;background:var(--white)}
body{position:relative;font-family:"Mulish",sans-serif;color:var(--text)}
.abs{position:absolute}

/* hero */
.hero{position:absolute;left:0;top:0;width:724px;height:276px;background:radial-gradient(ellipse at 40% 40%,#5b5047 0%,#3a332e 45%,#221e1b 100%)}
.brand{position:absolute;display:flex;align-items:center;gap:8px;font-family:"Montserrat",sans-serif;font-weight:500;font-size:13px;color:var(--orange)}
.brand-dot{width:22px;height:22px;border-radius:50%;border:1.5px solid currentColor}
.nav{position:absolute;right:79px;top:19px;display:flex;align-items:center;gap:19px;font-size:8.3px;color:var(--white)}
.nav .login{background:var(--orange);padding:5px 8px;font-family:"Montserrat",sans-serif;font-weight:700}
.hero-title{position:absolute;top:94px;width:724px;text-align:center;font-family:"Montserrat",sans-serif;font-weight:800;font-size:17px;color:var(--white)}
.hero-lead{position:absolute;top:128px;width:724px;text-align:center;font-size:10px;line-height:16px;color:#f1ece8}
.cta{position:absolute;left:300px;top:176px;width:125px;height:27px;background:var(--orange);color:var(--white);font-family:"Montserrat",sans-serif;font-weight:700;font-size:9.5px;display:flex;align-items:center;justify-content:center}

/* section headings */
.section-title{position:absolute;width:724px;text-align:center;font-family:"Montserrat",sans-serif;font-weight:700;font-size:11.5px;color:var(--ink)}
.rule{position:absolute;height:1.5px;background:#555}

/* steps */
.steps{position:absolute;left:0;top:340px}
.step{position:absolute;width:120px;text-align:center}
.step h3{font-family:"Montserrat",sans-serif;font-weight:700;font-size:7.3px;color:var(--ink);margin-bottom:8px}
.step p{font-size:6.2px;line-height:8.7px;color:var(--muted)}

/* overview */
.overview{position:absolute;left:0;top:595px;width:724px;height:240px;background:var(--panel)}
.overview-art{position:absolute;left:95px;top:35px;width:155px;height:160px;border-radius:50%;background:radial-gradient(circle,#f5f4f5 55%,#f3d3c6 56%,#f3d3c6 62%,#f5f4f5 63%)}
.divider{position:absolute;left:305px;top:33px;width:1px;height:172px;background:#cfcfcf}
.overview h2{position:absolute;left:366px;top:32px;font-family:"Montserrat",sans-serif;font-weight:800;font-size:11.5px;color:var(--ink)}
.overview-copy{position:absolute;left:366px;top:70px;width:277px;font-size:8.4px;line-height:13.6px;color:var(--text);text-align:justify}
.overview-copy p+p{margin-top:13px}

/* organizers */
.card{position:absolute;top:911px;width:127px;height:200px;border:1px solid #dcdcdc;background:var(--white);text-align:center}
.card-photo{height:111px}
.card h4{font-family:"Montserrat",sans-serif;font-weight:500;font-size:8.5px;color:var(--ink);margin:15px 0 7px;letter-spacing:.3px}
.card p{font-size:7.6px;line-height:11.2px;color:var(--text)}

/* footer */
.footer{position:absolute;left:0;top:1138px;width:724px;height:62px;background:var(--footer)}
.copyright{position:absolute;right:79px;top:27px;font-size:7px;color:#cfcfcf}
</style>
</head>
<body>

<header class="hero" role="img" aria-label="Crowd of demonstrators raising fists">
  <div class="brand" style="left:80px;top:19px;color:var(--orange)"><span class="brand-dot"></span>Pelbo</div>
  <nav class="nav">
    <span>Post Action</span><span>Your action</span><span>Register</span><span class="login">Login</span>
  </nav>
  <h1 class="hero-title">RACIAL JUSTICE</h1>
  <p class="hero-lead">Lorem Ipsum is simply dummy text of the printing and types<br>etting industry lorem Ipsum has been the industry.</p>
  <a class="cta">Quill web store</a>
</header>

<h2 class="section-title" style="top:302px">HOW THE QUILL EXTENSION WORKS</h2>
<div class="rule" style="left:347px;top:330px;width:16px"></div>

<svg class="steps" width="724" height="240" viewBox="0 0 724 240">
  <defs>
    <filter id="lift" x="-30%" y="-30%" width="160%" height="170%">
      <feDropShadow dx="0" dy="10" stdDeviation="9" flood-color="#000" flood-opacity=".12"/>
    </filter>
    <marker id="head" viewBox="0 0 10 10" refX="5" refY="5" markerWidth="5" markerHeight="5" orient="auto">
      <path d="M0 0L10 5L0 10z" fill="var(--orange)"/>
    </marker>
    <marker id="head2" viewBox="0 0 10 10" refX="5" refY="5" markerWidth="5" markerHeight="5" orient="auto">
      <path d="M0 0L10 5L0 10z" fill="var(--orange-mid)"/>
    </marker>
  </defs>
  <path d="M95 41 Q169 -20 238 38" fill="none" stroke="var(--orange)" stroke-width="2" marker-end="url(#head)"/>
  <path d="M482 41 Q556 -20 625 38" fill="none" stroke="var(--orange)" stroke-width="2" marker-end="url(#head)"/>
  <path d="M289 188 Q362 250 431 192" fill="none" stroke="var(--orange-mid)" stroke-width="2" marker-end="url(#head2)"/>

  <g filter="url(#lift)" fill="var(--white)">
    <circle cx="169" cy="115" r="89"/><circle cx="362" cy="115" r="89"/><circle cx="558" cy="115" r="89"/>
  </g>
  <circle cx="169" cy="115" r="81" fill="none" stroke="var(--orange)" stroke-width="5"/>
  <circle cx="362" cy="115" r="81" fill="none" stroke="var(--orange-mid)" stroke-width="5"/>
  <circle cx="558" cy="115" r="81" fill="none" stroke="var(--orange-soft)" stroke-width="5"/>

  <g stroke="var(--ink)" stroke-width="1.5" fill="var(--white)">
    <line x1="249" y1="112" x2="281" y2="112"/><line x1="444" y1="112" x2="476" y2="112"/>
    <circle cx="249" cy="112" r="5.5"/><circle cx="281" cy="112" r="5.5"/>
    <circle cx="444" cy="112" r="5.5"/><circle cx="476" cy="112" r="5.5"/>
  </g>

  <g fill="none" stroke="var(--orange)" stroke-width="1.4">
    <circle cx="164" cy="72" r="12"/><circle cx="164" cy="72" r="5"/>
    <path d="M172 86 L186 62 L190 64 L176 88 Z"/>
    <path d="M352 58 h16 v28 h-16 z M356 66 h8 M356 72 h8 M356 78 h8"/>
    <path d="M368 72 h5 v14 h-5"/>
    <circle cx="558" cy="74" r="15"/>
  </g>
</svg>

<div class="step" style="left:109px;top:442px"><h3>LOREM IPSUM</h3><p>There are many variations of passages of Lorem Ipsum available, but the majority have suffered alteration in some form, by injected humour, or randomised</p></div>
<div class="step" style="left:302px;top:442px"><h3>LOREM IPSUM</h3><p>There are many variations of passages of Lorem Ipsum available, but the majority have suffered alteration in some form, by injected humour, or randomised</p></div>
<div class="step" style="left:498px;top:442px"><h3>LOREM IPSUM</h3><p>There are many variations of passages of Lorem Ipsum available, but the majority have suffered alteration in some form, by injected humour, or randomised</p></div>

<section class="overview">
  <div class="overview-art" role="img" aria-label="Illustration of four people linked in a circle"></div>
  <div class="divider"></div>
  <h2>OVERVIEW</h2>
  <div class="rule" style="left:366px;top:52px;width:63px"></div>
  <div class="overview-copy">
    <p>Facilitating social responsibility by connecting like minded individuals and to ways they may impact the real world</p>
    <p>Many of us read about social and political issues we care about every day, but may not know how to take concrete action to combat injustice and create meaningful change. Pelbo is a Quill extension that analyzes articles you are reading and recommends relevant actions you can take. By connecting you to organizers and movements, Pelbo can help you find ways to take part in building a more just, equitable, and sustainable future.</p>
  </div>
</section>

<h2 class="section-title" style="top:864px">ORGANIZERS</h2>
<div class="rule" style="left:322px;top:884px;width:80px"></div>

<article class="card" style="left:80px"><div class="card-photo" role="img" aria-label="Portrait of Stephen" style="background:linear-gradient(#c9d2d8,#a9b4bc)"></div><h4>STEPHEN</h4><p>Lorem Ipsum is simply<br>dummy text of the printing<br>and typesetting industry</p></article>
<article class="card" style="left:225px"><div class="card-photo" role="img" aria-label="Portrait of Deleon" style="background:linear-gradient(#b7bdb8,#7f8a86)"></div><h4>DELEON</h4><p>Lorem Ipsum is simply<br>dummy text of the printing<br>and typesetting industry</p></article>
<article class="card" style="left:371px"><div class="card-photo" role="img" aria-label="Portrait of Mary" style="background:linear-gradient(#d9dde0,#6d7f99)"></div><h4>MARY</h4><p>Lorem Ipsum is simply<br>dummy text of the printing<br>and typesetting industry</p></article>
<article class="card" style="left:517px"><div class="card-photo" role="img" aria-label="Portrait of West" style="background:linear-gradient(#a88a72,#6e5444)"></div><h4>WEST</h4><p>Lorem Ipsum is simply<br>dummy text of the printing<br>and typesetting industry</p></article>

<footer class="footer">
  <div class="brand" style="left:80px;top:20px"><span class="brand-dot"></span>Pelbo</div>
  <p class="copyright">Copyright © 2022 All Rights Reserved</p>
</footer>

</body>
</html>
```